Flowmark Engineering Business Card

our company has just rebranded and taken on a new logo design. We now need to update our business cards with the new logo. This is also an opportunity to reformat and modernize our look. We are an engineering company so the look needs to be formal and professional yet it should look modern. Have a look at our current card and the new card should have the same information.

Target Market(s)

Engineering firms, government, mining companies

Industry/Entity Type

Mechanical Engineering

Contact Information for Business Card

see example attached

Requirements
Must have
• look professional and modern
Should not have
• should not include the office locations 'Brisbane, Sydney and Kuala Lumpur'
• you will find this on the example but it should not be included in these versions. please remove from your submissions and resubmit

```html
<!DOCTYPE html>
<html lang="en">
<head>
<meta charset="utf-8">
<title>Flowmark Engineering Business Card</title>
<link rel="stylesheet" href="https://fonts.googleapis.com/css2?family=Open+Sans:wght@400;600;700&display=swap">
<style>
  :root {
    --backdrop: #d8d9db;
    --card: #ffffff;
    --brand-blue: #3b45a6;
    --accent-teal: #2bb5c8;
    --text-grey: #5a5a5a;
    --shadow: rgba(0, 0, 0, 0.18);
  }
  * { box-sizing: border-box; margin: 0; padding: 0; }
  html, body {
    width: 1200px;
    height: 902px;
    overflow: hidden;
  }
  body {
    background: var(--backdrop);
    font-family: "Open Sans", Arial, sans-serif;
    color: var(--text-grey);
    position: relative;
  }
  .card {
    position: absolute;
    left: 300px;
    width: 600px;
    height: 343px;
    background: var(--card);
    box-shadow: 0 10px 28px var(--shadow);
  }
  .card--front { top: 70px; }
  .card--back { top: 482px; }

  .wordmark {
    position: absolute;
    display: flex;
    align-items: center;
    gap: 12px;
  }
  .wordmark__dot {
    width: 30px;
    height: 30px;
    border-radius: 50%;
    background: var(--brand-blue);
    flex: none;
  }
  .wordmark__name {
    font-weight: 700;
    font-size: 27px;
    line-height: 1.05;
    color: var(--brand-blue);
    letter-spacing: 0.5px;
    text-transform: uppercase;
  }
  .card--front .wordmark { left: 48px; top: 118px; }
  .card--back .wordmark { left: 48px; top: 236px; }

  .contact {
    position: absolute;
    right: 40px;
    top: 54px;
    text-align: right;
    font-size: 12.5px;
    line-height: 1.6;
  }
  .contact__line {
    display: flex;
    justify-content: flex-end;
    align-items: center;
    gap: 6px;
  }
  .contact__icon { width: 12px; height: 12px; flex: none; }
  .contact__address { margin-bottom: 8px; }

  .website {
    position: absolute;
    left: 48px;
    bottom: 34px;
    font-size: 15px;
    letter-spacing: 2px;
  }
  .website__domain { color: var(--accent-teal); font-weight: 600; }

  .person {
    position: absolute;
    right: 48px;
    top: 104px;
    text-align: right;
  }
  .person__name {
    font-weight: 600;
    font-size: 17px;
    color: var(--accent-teal);
  }
  .person__role {
    font-size: 15px;
    color: var(--text-grey);
  }
</style>
</head>
<body>

  <section class="card card--front" aria-label="Business card front">
    <div class="wordmark">
      <span class="wordmark__dot"></span>
      <span class="wordmark__name">Flowmark<br>Engineering</span>
    </div>

    <address class="contact" style="font-style: normal;">
      <div class="contact__address">2218 Cedar Hollow Rd<br>Austin TX 78731</div>
      <div class="contact__line">512.000.4417
        <svg class="contact__icon" viewBox="0 0 24 24" aria-hidden="true"><path fill="var(--accent-teal)" d="M6.6 10.8a15.1 15.1 0 0 0 6.6 6.6l2.2-2.2a1 1 0 0 1 1-.25 11.4 11.4 0 0 0 3.6.57 1 1 0 0 1 1 1V20a1 1 0 0 1-1 1A17 17 0 0 1 3 4a1 1 0 0 1 1-1h3.5a1 1 0 0 1 1 1c0 1.25.2 2.45.57 3.57a1 1 0 0 1-.25 1z"/></svg>
      </div>
      <div class="contact__line">dana@flowmarkeng.com
        <svg class="contact__icon" viewBox="0 0 24 24" aria-hidden="true"><rect x="2" y="5" width="20" height="14" rx="1.5" fill="var(--accent-teal)"/><path d="M3 6l9 7 9-7" fill="none" stroke="#fff" stroke-width="1.6"/></svg>
      </div>
    </address>

    <div class="website">www.<span class="website__domain">flowmarkeng</span>.com</div>
  </section>

  <section class="card card--back" aria-label="Business card back">
    <div class="person">
      <div class="person__name">Dana Whitfield</div>
      <div class="person__role">Owner</div>
    </div>

    <div class="wordmark">
      <span class="wordmark__dot"></span>
      <span class="wordmark__name">Flowmark<br>Engineering</span>
    </div>
  </section>

</body>
</html>
```